Business Cards - Brightpath Horizon

need to design unique business card for my mortgage business. I need to design credit card style business card for my business or any unique idea that you might have

Target Market(s)

Home Loan customers

Industry/Entity Type

Mortgage Brokerage

Contact Information for Business Card

please design credit card style or very unique style business card

Colors

Designer to choose colors to be used in the design.

Requirements
Must have
• Name
• position
• Phone number
• fax number
• email address
• website address
• social media address
• All above fields will be provided once design in finalised

```html
<!DOCTYPE html>
<html lang="en">
<head>
<meta charset="utf-8">
<title>Brightpath Horizon – Business Card</title>
<link rel="stylesheet" href="https://fonts.googleapis.com/css2?family=Roboto:wght@400;700&family=Roboto+Condensed:wght@700&family=Playfair+Display:ital,wght@1,400&display=swap">
<style>
  :root {
    --bg: #e9e6e1;
    --card-white: #fbfbfb;
    --brand-blue: #0a31d6;
    --brand-orange: #f28a1e;
    --brand-orange-light: #f6a24a;
    --ink: #3b3b3b;
    --white: #ffffff;
  }
  * { margin: 0; padding: 0; box-sizing: border-box; }
  html, body { width: 1200px; height: 911px; overflow: hidden; background: var(--bg); }
  .canvas {
    width: 1200px; height: 911px;
    display: flex; flex-direction: column; align-items: center; justify-content: center; gap: 36px;
  }
  .card {
    position: relative; width: 640px; height: 404px; border-radius: 22px; overflow: hidden;
    box-shadow: 0 6px 18px rgba(0,0,0,.18);
  }
  .card-front { background: var(--card-white); }
  .card-back { background: var(--brand-blue); }

  .feature-art {
    position: absolute; inset: 0;
    background: linear-gradient(135deg, var(--brand-orange-light), var(--brand-orange));
    clip-path: polygon(100% 17%, 100% 100%, 66% 100%, 59% 62%);
  }

  .holder { position: absolute; top: 40px; right: 44px; text-align: right; font-family: "Roboto Condensed", sans-serif; text-transform: uppercase; }
  .holder-name { color: var(--brand-blue); font-size: 22px; font-weight: 700; letter-spacing: .5px; }
  .holder-role { color: var(--brand-orange); font-size: 16px; font-weight: 700; margin-top: 2px; }

  .brand { position: absolute; left: 44px; top: 92px; }
  .brand-name { display: flex; align-items: center; gap: 10px; white-space: nowrap; font-family: "Roboto", sans-serif; font-weight: 700; font-size: 30px; color: var(--brand-blue); text-transform: uppercase; letter-spacing: 1px; }
  .brand-mark { width: 16px; height: 16px; border-radius: 50%; background: var(--brand-blue); flex: none; }
  .tagline { font-family: "Playfair Display", serif; font-style: italic; font-size: 17px; color: var(--brand-orange); margin: 6px 0 0 26px; white-space: nowrap; }

  .contact { position: absolute; left: 44px; bottom: 36px; font-family: "Roboto", sans-serif; font-size: 14.5px; color: var(--ink); line-height: 1.45; }
  .address { margin-bottom: 10px; }
  .contact-line { display: flex; align-items: center; gap: 9px; }
  .contact-line svg { width: 12px; height: 12px; flex: none; fill: var(--brand-blue); }

  .back-brand { position: absolute; left: 0; right: 0; top: 44%; transform: translateY(-50%); text-align: center; color: var(--white); }
  .back-brand .brand-name { color: var(--white); font-size: 36px; justify-content: center; }
  .back-brand .brand-mark { width: 20px; height: 20px; background: var(--white); }
  .back-brand .tagline { color: var(--white); font-size: 20px; margin: 10px 0 0; }

  .social { position: absolute; left: 50%; bottom: 70px; transform: translateX(-50%); display: flex; gap: 12px; }
  .social-dot { width: 26px; height: 26px; border-radius: 50%; background: var(--white); }
</style>
</head>
<body>
<main class="canvas">
  <section class="card card-front" aria-label="Card front">
    <div class="feature-art" role="img" aria-label="Orange illustration of stacked house roofs with windows"></div>

    <div class="holder">
      <p class="holder-name">Daniel Reyes</p>
      <p class="holder-role">CEO/Founder</p>
    </div>

    <div class="brand">
      <p class="brand-name"><span class="brand-mark"></span>Brightpath Horizon</p>
      <p class="tagline">Smart loans, Secure homes</p>
    </div>

    <div class="contact">
      <p class="address">214 Willow Bend Road<br>Fairbanks, Alaska 99701</p>
      <p class="contact-line"><svg viewBox="0 0 12 12"><path d="M2 1h3l1 3-2 1a7 7 0 0 0 3 3l1-2 3 1v3c-6 0-10-4-10-9z"/></svg>907 555 0148</p>
      <p class="contact-line"><svg viewBox="0 0 12 12"><rect x="2" y="4" width="8" height="7"/><rect x="3" y="1" width="6" height="3"/></svg>907 555 0193</p>
      <p class="contact-line"><svg viewBox="0 0 12 12"><path d="M1 3h10v7H1z M1 3l5 4 5-4"/></svg>hello@brightpathhorizon.com</p>
      <p class="contact-line"><svg viewBox="0 0 12 12"><circle cx="6" cy="6" r="5.5"/></svg>www.brightpathhorizon.com</p>
    </div>
  </section>

  <section class="card card-back" aria-label="Card back">
    <div class="back-brand">
      <p class="brand-name"><span class="brand-mark"></span>Brightpath Horizon</p>
      <p class="tagline">Smart loans, Secure homes</p>
    </div>
    <div class="social" aria-label="Social media links">
      <span class="social-dot"></span>
      <span class="social-dot"></span>
      <span class="social-dot"></span>
      <span class="social-dot"></span>
    </div>
  </section>
</main>
</body>
</html>
```